Brochure design for International Beauty Trade Show

I neee a tri-fold company products' brochure to distribute to customers at an international trade show coming soon. We have 4 main product categories- hair and skincare, facial care, Body and bath and massage oil.
The brochure needs to include at least 2 photos of the main products of each category, benefits, call to action and our company contact info ( website and phone number).

Target Market(s)

Educated and high income earners looking for all-natural,pure, 100 organic products for their beauty and personal care needs. Our products cross all racial groups/demographics and suitable for all skin types

Industry/Entity Type

Hair And Beauty

Font styles to use
Serif

Colors

Designer to choose colors to be used in the design.

Requirements
Must have
• The design must stand out as pure and luxury and at the same time be inclusive using our logo design colors- orange and blue. Also, the content must be easy to read and captivating.
• Finally if using women pictures, please include Black, white, Asian and Latina to reflect the fact that our products are suitable for all skin types.
Nice to have
• Design the brochure such that it could be printed as a poster-banner ad.
Should not have
• Cookie cutter designs are not welcome

```html
<!DOCTYPE html>
<html lang="en">
<head>
<meta charset="utf-8">
<title>Lumera Solutions – Product Brochure</title>
<link rel="stylesheet" href="https://fonts.googleapis.com/css2?family=Questrial&family=Exo+2:wght@600;700&family=Oswald:wght@300;500&display=swap">
<style>
:root{
  --orange:#f26a10;
  --blue:#1e88d6;
  --yellow:#f7e11b;
  --ink:#1d1d1d;
  --white:#ffffff;
  --stage:#e8e5e0;
}
*{margin:0;padding:0;box-sizing:border-box}
html,body{width:960px;height:1200px;overflow:hidden;background:var(--stage)}
body{position:relative;font-family:"Questrial",sans-serif;color:var(--ink)}
.sheet{position:absolute;left:118px;width:818px;height:632px;background:var(--white);
  transform:scale(.885);transform-origin:0 0;overflow:hidden;box-shadow:0 4px 14px rgba(0,0,0,.18)}
.sheet--outer{top:20px}
.sheet--inner{top:620px}
.art{position:absolute;inset:0;width:818px;height:632px}
.abs{position:absolute}

/* outer headings */
.about-title{left:24px;top:28px;font-family:"Exo 2",sans-serif;font-weight:700;font-size:24px;color:var(--yellow)}
.about-text{left:24px;top:64px;width:212px;font-size:12.5px;line-height:16.6px;color:var(--white)}
.range-title{left:24px;top:256px;font-family:"Exo 2",sans-serif;font-weight:600;font-size:16px;line-height:22px;color:var(--blue)}

/* lists */
.benefits{list-style:none;font-size:12.5px}
.benefits li{position:relative;padding-left:24px;line-height:14px;margin-bottom:8.5px}
.benefits--bold{font-size:12px}
.benefits--bold li{font-weight:700;-webkit-text-stroke:.2px currentColor}
.benefits li::before{content:"";position:absolute;left:2px;top:0;width:11px;height:11px;border:1.5px solid var(--tick)}
.benefits li::after{content:"";position:absolute;left:6px;top:-2px;width:5px;height:10px;border:solid var(--tick);border-width:0 2px 2px 0;transform:rotate(40deg)}
.benefits--blue{--tick:var(--blue)}
.benefits--orange{--tick:var(--orange)}
.range-list{left:26px;top:312px;width:212px}
.range-list li{margin-bottom:10px}

/* call to action */
.order-pill{left:0;top:581px;width:257px;height:28px;background:var(--orange);border-radius:0 14px 14px 0;
  color:var(--white);font-family:"Exo 2",sans-serif;font-weight:600;font-size:11.5px;line-height:28px;padding-left:61px}
.order-icon{left:20px;top:577px;width:34px;height:34px;border-radius:50%;background:var(--white);border:2px solid var(--orange)}

/* brand block */
.brand-mark{left:360px;top:372px;width:100px;height:100px;border-radius:50%;background:var(--orange)}
.contact{left:310px;top:518px;width:200px;text-align:center;font-family:"Exo 2",sans-serif;font-weight:600;font-size:13.5px;line-height:22.5px;font-style:normal}
.brand-name{left:590px;top:462px;display:flex;align-items:center;gap:9px;white-space:nowrap}
.brand-dot{width:28px;height:28px;border-radius:50%;background:var(--orange)}
.brand-word{font-family:"Questrial",sans-serif;font-size:17px;letter-spacing:1px;color:var(--blue);line-height:1}
.tagline{left:555px;top:524px;width:250px;text-align:center;font-family:"Oswald",sans-serif;line-height:38px}
.tagline-main{display:block;font-weight:500;font-size:34px;color:var(--orange)}
.tagline-sub{display:block;font-weight:300;font-size:31px;color:var(--blue)}

/* inner side */
.cat-title{font-family:"Exo 2",sans-serif;font-weight:600;font-size:23px;line-height:28px;white-space:nowrap}
.cat-title--orange{color:var(--orange)}
.cat-title--blue{color:var(--blue)}
.bar{height:23px;border-radius:12px;color:var(--white);font-family:"Exo 2",sans-serif;font-weight:600;font-size:12.5px;line-height:23px;padding-left:26px}
.bar--orange{background:var(--orange)}
.bar--blue{background:var(--blue)}
.photo{border-radius:4px}
</style>
</head>
<body>

<!-- Outer side -->
<section class="sheet sheet--outer">
  <svg class="art" viewBox="0 0 818 632">
    <defs>
      <linearGradient id="greenWash" x1="0" y1="0" x2="1" y2="0.4">
        <stop offset="0" stop-color="#1f6a1a"/>
        <stop offset=".55" stop-color="#6fb52e"/>
        <stop offset="1" stop-color="#3d2a24"/>
      </linearGradient>
    </defs>
    <path role="img" aria-label="Spa photograph: bamboo leaves, purple orchid, black stones and a woman with long dark hair"
      d="M0 0 H818 V335 C700,400 520,330 380,262 C300,226 160,205 0,245 Z" fill="url(#greenWash)"/>
    <path d="M0 245 C160,205 300,226 380,262 C520,330 700,400 818,335 V352 C700,420 520,352 380,284 C300,248 160,226 0,258 Z" fill="var(--orange)"/>
    <path d="M290 268 C450,330 640,435 818,396" fill="none" stroke="var(--blue)" stroke-width="6"/>
  </svg>

  <h2 class="abs about-title">About Us</h2>
  <p class="abs about-text">Lumera Solutions is an export/import company. Our mission is to satisfy our customers by supplying them with pure, 100% organic products, that make them more attractive and solve the most common skin and hair problems</p>

  <h3 class="abs range-title">Over 20 luxury Products<br>to choose from including:</h3>
  <ul class="abs benefits benefits--blue range-list">
    <li>Argan oil</li>
    <li>Prickly Pear seed oil</li>
    <li>Carrot oil</li>
    <li>Moroccan Beldi Soap</li>
    <li>Green Clay Mask</li>
    <li>Butter</li>
    <li>Mineral and vegetable based<br>bar soaps</li>
    <li>Shea Butter</li>
    <li>Stretch marks/vergeture oil</li>
    <li>Massage oil</li>
  </ul>

  <div class="abs order-pill">Place your order at lumera-co.com</div>
  <div class="abs order-icon"></div>

  <div class="abs brand-mark"></div>
  <address class="abs contact">
    (800) 555-0147<br>hello@lumera-co.com<br>www.lumera-co.com
  </address>

  <div class="abs brand-name"><span class="brand-dot"></span><span class="brand-word">LUMERA SOLUTIONS</span></div>
  <p class="abs tagline"><span class="tagline-main">Natural Solutions</span><span class="tagline-sub">to Forever Beauty</span></p>
</section>

<!-- Inner side -->
<section class="sheet sheet--inner">
  <svg class="art" viewBox="0 0 818 632">
    <defs>
      <linearGradient id="softLeaf" x1="0" y1="0" x2="1" y2="0">
        <stop offset="0" stop-color="#f6f6f2"/>
        <stop offset=".5" stop-color="#e7efd9"/>
        <stop offset="1" stop-color="#7fb83a"/>
      </linearGradient>
    </defs>
    <path role="img" aria-label="Soft green leaf backdrop photograph"
      d="M0 0 H818 V68 C650,78 520,132 360,146 C260,152 150,140 0,124 Z" fill="url(#softLeaf)"/>
    <path d="M0 124 C150,140 260,152 360,146 C520,132 650,78 818,68" fill="none" stroke="var(--orange)" stroke-width="9"/>
    <path d="M0 142 C150,156 260,165 360,160 C520,148 650,98 818,90" fill="none" stroke="var(--blue)" stroke-width="5"/>
  </svg>

  <div class="abs photo" role="img" aria-label="Portrait of a woman with curly dark hair" style="left:0;top:0;width:220px;height:130px;background:linear-gradient(135deg,#5a3a2a,#c9a58a)"></div>
  <div class="abs photo" role="img" aria-label="Hair and skin oil bottles with an argan oil capsule" style="left:80px;top:120px;width:155px;height:240px;background:linear-gradient(180deg,#e8d6b8,#b06a1e)"></div>
  <div class="abs photo" role="img" aria-label="Facial soap boxes with lemons and prickly pears" style="left:560px;top:4px;width:222px;height:155px;background:linear-gradient(135deg,#9fd3a0,#3f6bb5 60%,#c8324a)"></div>
  <div class="abs photo" role="img" aria-label="Clay mask jar and soap box" style="left:410px;top:284px;width:118px;height:132px;background:linear-gradient(160deg,#f3f3ee,#9ccf9b)"></div>
  <div class="abs photo" role="img" aria-label="Woman wrapped in a white towel seated on the floor" style="left:300px;top:432px;width:270px;height:200px;background:linear-gradient(160deg,#f4ede6,#dcc0a8)"></div>
  <div class="abs photo" role="img" aria-label="Massage oil spray bottle" style="left:744px;top:460px;width:48px;height:145px;background:linear-gradient(180deg,#d9dbe6,#2c2f6b 55%,#4a2a5a)"></div>
  <div class="abs photo" role="img" aria-label="Red berries" style="left:685px;top:568px;width:58px;height:44px;background:linear-gradient(135deg,#e05050,#8a1a1a)"></div>

  <h3 class="abs cat-title cat-title--orange" style="left:25px;top:366px">Hair &amp; Skincare</h3>
  <div class="abs bar bar--orange" style="left:0;top:406px;width:230px;border-radius:0 12px 12px 0">BENEFITS</div>
  <ul class="abs benefits benefits--orange benefits--bold" style="left:24px;top:446px;width:260px">
    <li>Natural moisturizer</li>
    <li>Heal damaged hair or sensitive scalp</li>
    <li>Soften curly and frizzy hair</li>
    <li>Antiaging, remove wrinkles</li>
    <li>Reduce sebum secretion</li>
    <li>Tone, sooth and restore luster</li>
    <li>Restore fair complexion</li>
  </ul>

  <h3 class="abs cat-title cat-title--blue" style="left:295px;top:168px">Facial Care</h3>
  <div class="abs bar bar--blue" style="left:270px;top:201px;width:230px">BENEFITS</div>
  <ul class="abs benefits benefits--blue benefits--bold" style="left:295px;top:238px;width:220px">
    <li>Reduce sebum secretion</li>
    <li>Eliminate toxins &amp; blemishes</li>
    <li>Tighten pores</li>
    <li>Dries pimples</li>
    <li>Remove<br>blackheads</li>
  </ul>

  <h3 class="abs cat-title cat-title--orange" style="left:574px;top:168px">Body &amp; Bath Care</h3>
  <div class="abs bar bar--orange" style="left:546px;top:202px;width:230px">BENEFITS</div>
  <ul class="abs benefits benefits--orange benefits--bold" style="left:578px;top:241px;width:220px">
    <li>Purify and disinfect</li>
    <li>Fight &nbsp;acne</li>
    <li>Rejuvenate &amp; hydrate</li>
    <li>Promote healthy looking skin</li>
    <li>Remove dead cells</li>
  </ul>

  <h3 class="abs cat-title cat-title--blue" style="left:574px;top:387px">Massage Care</h3>
  <div class="abs bar bar--blue" style="left:546px;top:421px;width:230px">BENEFITS</div>
  <ul class="abs benefits benefits--blue benefits--bold" style="left:578px;top:460px;width:162px">
    <li>Relief stress and pain</li>
    <li>Fight muscle<br>contraction/tenderness</li>
    <li>Eliminate stretch marks</li>
    <li>Pure, undiluted</li>
  </ul>
</section>

</body>
</html>
```